Copperleaf Venture Trust

Take current power point presentation and make it uniform in color and font, and create designs that pop throughout the presentation. Right now, it is dull and mundane.

```html
<!DOCTYPE html>
<html lang="en">
<head>
<meta charset="utf-8">
<title>Copperleaf Venture Trust – Presentation</title>
<link href="https://fonts.googleapis.com/css2?family=Poppins:wght@400;500;600;700&display=swap" rel="stylesheet">
<style>
:root{
  --blue:#0070c0;
  --grey:#5f6062;
  --ink:#2d2d2d;
  --band:#e4f1fb;
  --page:#ffffff;
  --glow:rgba(0,112,192,.16);
}
*{box-sizing:border-box;margin:0;padding:0}
html,body{width:1004px;height:1200px;overflow:hidden;background:var(--page);font-family:'Poppins',sans-serif;color:var(--ink)}
.deck{position:relative;width:1004px;height:1200px}
.slide{position:absolute;width:469px;height:263px;background:#fff;box-shadow:0 4px 18px var(--glow);overflow:hidden}
.col-l{left:25px}.col-r{left:511px}
.row1{top:26px}.row2{top:316px}.row3{top:607px}.row4{top:904px}
.head{position:absolute;left:0;top:0;width:469px;height:37px}
.head svg{position:absolute;left:0;top:0}
.brand{position:absolute;left:23px;top:5px;font-weight:700;font-size:19px;color:var(--blue);letter-spacing:.5px}
.head-title{position:absolute;right:23px;top:7px;font-weight:700;font-size:14.5px;color:#fff}
.foot-date{position:absolute;left:23px;bottom:6px;font-size:5.8px;font-weight:600;color:var(--ink)}
.foot-page{position:absolute;right:24px;bottom:6px;font-size:5.8px;font-weight:600;color:var(--blue)}
.abs{position:absolute}
.h-blue{color:var(--blue);font-weight:600;font-size:9.5px}
.body{font-size:6.2px;line-height:13.4px;color:var(--ink)}
.photo{position:absolute;border-radius:9px}

/* cover */
.cover-brand{position:absolute;left:23px;top:40px;font-weight:700;font-size:40px;color:var(--blue);letter-spacing:1px}
.cover-title{position:absolute;left:23px;top:110px;font-weight:700;font-size:19.5px;line-height:26.5px}
.cover-title .t1{color:var(--blue)}.cover-title .t2{color:var(--grey)}
.cover-desc{position:absolute;left:23px;top:200px;width:230px;font-size:6.8px;line-height:12px;color:var(--grey)}
.hex-collage{position:absolute;left:133px;top:9px}

/* toc */
.toc{position:absolute;left:0;top:49px;width:443px}
.toc-row{position:relative;height:13.4px;font-size:7.4px;line-height:13.4px}
.toc-row.main{background:var(--band);margin-bottom:0}
.toc-row .num{position:absolute;left:23px;color:var(--blue);font-weight:600}
.toc-row .lbl{position:absolute;right:2px}
.toc-row.main .lbl{color:var(--blue);font-weight:600}

/* bullets */
.bullets{list-style:none}
.bullets li{position:relative;padding-left:10px}
.bullets li::before{content:"";position:absolute;left:0;top:3.8px;width:5.5px;height:5.5px;border-radius:50%;background:var(--ink)}
.bullets li::after{content:"";position:absolute;left:1.4px;top:5.9px;width:2.4px;height:1.4px;border-right:1.4px solid #fff;border-top:0;background:#fff;transform:none}
.bullets li .tip{display:none}

/* org chart */
.org-top{position:absolute;left:87px;top:81px;width:109px;height:23px;border-radius:8px;background:var(--blue);color:#fff;font-size:7.6px;font-weight:500;display:flex;align-items:center;justify-content:center}
.org-member{position:absolute;width:66px;height:42px;border-radius:4px;background:var(--grey);color:#fff;font-size:6.8px;line-height:12px;font-weight:500;display:flex;align-items:center;justify-content:center;text-align:center}
.right-txt{text-align:right}

/* team */
.card{position:absolute;top:58px;width:126px;height:178px;border:1px solid var(--grey);background:#fff}
.card .pic{height:68px;background:linear-gradient(160deg,#3a3a3a,#8b8b8b 60%,#d4d4d4)}
.card .name{text-align:center;font-weight:600;font-size:7.6px;margin-top:4px}
.card .bio{text-align:center;font-size:3.9px;line-height:7.3px;padding:2px 5px 0;color:var(--ink)}

/* different */
.feature{position:absolute;top:112px;width:96px}
.feature .fh{height:23px;border-radius:3px 3px 0 0;color:#fff;font-size:6.8px;line-height:8px;font-weight:500;display:flex;align-items:center;justify-content:center;text-align:center}
.feature .fb{border-radius:0 0 3px 3px;color:#fff;font-size:5.8px;line-height:11px;font-weight:500;text-align:center;padding:6px 6px}
.bg-blue{background:var(--blue)}.bg-grey{background:var(--grey)}
</style>
</head>
<body>
<div class="deck">

<!-- shared header graphic -->
<svg width="0" height="0" style="position:absolute">
  <defs>
    <g id="head-shape">
      <rect x="0" y="33" width="469" height="4" fill="#5f6062"/>
      <polygon points="171,0 177,0 169,33 163,33" fill="#5f6062"/>
      <polygon points="179,0 469,0 469,33 171,33" fill="#0070c0"/>
    </g>
  </defs>
</svg>

<!-- Cover -->
<section class="slide col-l row1">
  <div class="cover-brand">CVT</div>
  <h1 class="cover-title"><span class="t1">Copperleaf</span><br><span class="t2">Venture<br>Trust</span></h1>
  <p class="cover-desc">CVT focuses on financing Development Stage, Emerging Growth, and Distressed public companies.</p>
  <svg class="hex-collage" width="336" height="246" viewBox="0 0 336 246" role="img" aria-label="Hexagon collage of photos showing smiling business professionals at a meeting table">
    <defs>
      <linearGradient id="hexg" x1="0" y1="0" x2="1" y2="1">
        <stop offset="0" stop-color="#c9d6e2"/>
        <stop offset=".55" stop-color="#9fa8ae"/>
        <stop offset="1" stop-color="#dfe5ea"/>
      </linearGradient>
    </defs>
    <polygon points="0,30 17,0 52,0 69,30 52,60 17,60" fill="url(#hexg)"/>
    <polygon points="70,70 88,40 160,0 250,0 330,30 336,140 280,190 210,246 150,240 120,180 60,150" fill="url(#hexg)"/>
  </svg>
</section>

<!-- Table of content -->
<section class="slide col-r row1">
  <div class="head"><svg width="469" height="37"><use href="#head-shape"/></svg><div class="brand">CVT</div><div class="head-title">Table of Content</div></div>
  <div class="toc">
    <div class="toc-row main"><span class="num">04</span><span class="lbl">Objectives</span></div>
    <div class="toc-row main"><span class="num">05</span><span class="lbl">Strategy</span></div>
    <div class="toc-row main"><span class="num">06</span><span class="lbl">The CVT organization</span></div>
    <div class="toc-row"><span class="lbl">Senior Management</span></div>
    <div class="toc-row"><span class="lbl">CVT’s competitive advantage</span></div>
    <div class="toc-row"><span class="lbl">How we are different</span></div>
    <div class="toc-row main"><span class="num">12</span><span class="lbl">Performance</span></div>
    <div class="toc-row main"><span class="num">19</span><span class="lbl">Structure &amp; Terms</span></div>
    <div class="toc-row main"><span class="num">20</span><span class="lbl">Why Direct Investments?</span></div>
    <div class="toc-row"><span class="lbl">Why CVT’ Direct Invest Strategy?</span></div>
    <div class="toc-row"><span class="lbl">Industry Overview</span></div>
    <div class="toc-row"><span class="lbl">Differentiation Between PIPEs and &nbsp;Direct Investments</span></div>
    <div class="toc-row"><span class="lbl">Capital/Deal Structure</span></div>
    <div class="toc-row"><span class="lbl">Process</span></div>
    <div class="toc-row"><span class="lbl">Protection/Risk</span></div>
  </div>
  <div class="foot-date">03 April 2024</div><div class="foot-page">Page No: 02</div>
</section>

<!-- Objectives -->
<section class="slide col-l row2">
  <div class="head"><svg width="469" height="37"><use href="#head-shape"/></svg><div class="brand">CVT</div><div class="head-title">Objectives</div></div>
  <div class="abs" style="left:23px;top:56px;width:255px">
    <h2 class="h-blue">Investment Goal</h2>
    <ul class="bullets body"><li>Superior risk-adjusted returns while preserving capital in all market environments.</li></ul>
    <h2 class="h-blue" style="margin-top:3px">Our Approach to Meeting Objectives</h2>
    <ul class="bullets body">
      <li>Strategically negotiate private investments in publicly traded companies.</li>
      <li>Offer alternative capital solutions for small and micro-cap public companies with market capitalizations up to $2 billion.</li>
      <li>Employ a specialized strategy for collateralized investments.</li>
      <li>Maintain a well-diversified portfolio through tranching and sub-tranching of investments and milestones.</li>
      <li>Execute investments over a 1- to 4-year horizon, ensuring liquidity opportunities throughout.</li>
    </ul>
  </div>
  <div class="photo" style="left:297px;top:64px;width:147px;height:164px;background:linear-gradient(160deg,#aebfcc,#5c6670 55%,#d9dfe4)" role="img" aria-label="Photo of a smiling businessman in glasses working at his desk"></div>
  <div class="foot-date">03 April 2024</div><div class="foot-page">Page No: 03</div>
</section>

<!-- Investment Strategy -->
<section class="slide col-r row2">
  <div class="head"><svg width="469" height="37"><use href="#head-shape"/></svg><div class="brand">CVT</div><div class="head-title">Investment Strategy</div></div>
  <div class="photo" style="left:23px;top:60px;width:147px;height:172px;background:linear-gradient(160deg,#4d8fc4,#26384a 55%,#6d7d8a)" role="img" aria-label="Photo of three business colleagues talking at a conference"></div>
  <div class="abs" style="left:198px;top:70px;width:250px">
    <h2 class="h-blue">CVT Funding Specialization</h2>
    <p class="body" style="line-height:12px;margin-top:1px">CVT focuses on financing Development Stage, Emerging Growth, and Distressed public companies. This is achieved through a structured approach, wherein investments are tranched over a one- to four-year timeframe.</p>
    <h2 class="h-blue" style="margin-top:6px">Our Approach to Meeting Objectives</h2>
    <p class="body">Our strategy serves three key purposes:<br>1. Minimize Dilution: Limits the dilution of the issuer's common stock.<br>2. Mitigate Risk: Reduces exposure by allowing cessation of further investment in the event of a material adverse change.<br>3. Protect Capital: Safeguards against losses stemming from fraud or corporate malfeasance.</p>
  </div>
  <div class="foot-date">03 April 2024</div><div class="foot-page">Page No: 04</div>
</section>

<!-- The Organization divider -->
<section class="slide col-l row3">
  <div class="head"><svg width="469" height="37"><use href="#head-shape"/></svg><div class="brand">CVT</div><div class="head-title">The Organization</div></div>
  <div class="abs" style="left:346px;top:52px;font-weight:700;font-size:40px;color:#e8f1f9;letter-spacing:1px">CVT</div>
  <div class="abs" role="img" aria-label="Line illustration of a hand holding a money bag beside a growing coin plant with rising arrows" style="left:0;top:77px;width:260px;height:143px;background:linear-gradient(120deg,#eef5fb,#cfe3f3 60%,#f4f4f4)"></div>
  <div class="abs right-txt" style="right:23px;top:125px;font-weight:600;font-size:12px;line-height:26.5px">The Organization<br>CVT's Competitive Advantage:<br>What Sets Us Apart</div>
  <div class="foot-date">03 April 2024</div><div class="foot-page">Page No: 05</div>
</section>

<!-- The CVT Organization -->
<section class="slide col-r row3">
  <div class="head"><svg width="469" height="37"><use href="#head-shape"/></svg><div class="brand">CVT</div><div class="head-title">The CVT Organization</div></div>
  <svg class="abs" style="left:0;top:0" width="469" height="263">
    <g stroke="#2d2d2d" stroke-width=".6" stroke-dasharray="2 1.5" fill="none">
      <line x1="128" y1="104" x2="58" y2="143"/>
      <line x1="141" y1="104" x2="141" y2="178"/>
      <line x1="154" y1="104" x2="224" y2="143"/>
    </g>
  </svg>
  <div class="org-top">CVT Investments, LLC</div>
  <div class="org-member" style="left:25px;top:143px">Daniel Reyes<br>- Member</div>
  <div class="org-member" style="left:109px;top:178px">Omar Kassim<br>- Member</div>
  <div class="org-member" style="left:192px;top:143px">Peter Holloway<br>- Member</div>
  <div class="abs right-txt" style="right:21px;top:78px;width:180px">
    <h2 class="h-blue">CVT's Competitive Advantage</h2>
    <p class="body" style="line-height:12px;margin-top:2px">CVT is industry-agnostic, with a focus on identifying "super value" companies that possess strong operating entities and capable management teams.</p>
    <p class="body" style="line-height:12px;margin-top:16px">Our flexible organizational structure allows us to tailor each investment to address specific challenges-or a series of challenges-faced by these typically undervalued issuers.</p>
  </div>
  <div class="foot-date">03 April 2024</div><div class="foot-page">Page No: 06</div>
</section>

<!-- Senior Management -->
<section class="slide col-l row4">
  <div class="head"><svg width="469" height="37"><use href="#head-shape"/></svg><div class="brand">CVT</div><div class="head-title">Senior Management</div></div>
  <article class="card" style="left:23px">
    <div class="pic" role="img" aria-label="Black and white portrait photo of Daniel Reyes"></div>
    <h3 class="name">Daniel Reyes</h3>
    <p class="bio">Daniel Reyes is a Founder and Member of CVT Investments LLC, bringing over 17 years of experience in private investment in public equity transactions. Before launching his own funds, he co-founded several investment funds and managed portfolios for a boutique family office. He earlier worked as an analyst for a large hedge fund, overseeing fifty-five portfolio companies focused on private equity financing.</p>
  </article>
  <article class="card" style="left:171px">
    <div class="pic" role="img" aria-label="Black and white portrait photo of Omar Kassim" style="background:linear-gradient(160deg,#e6e6e6,#9a9a9a 60%,#2e2e2e)"></div>
    <h3 class="name">Omar Kassim</h3>
    <p class="bio">Omar Kassim is a Founder and Member of CVT Investments LLC with extensive experience investing in publicly traded companies since 2011. His professional background spans roles at a class action administration firm and an IT company prior to his move into finance. He holds a law degree and a bachelor's degree in philosophy and politics.</p>
  </article>
  <article class="card" style="left:318px">
    <div class="pic" role="img" aria-label="Black and white portrait photo of Peter Holloway" style="background:linear-gradient(160deg,#555,#b5b5b5 55%,#444)"></div>
    <h3 class="name">Peter Holloway</h3>
    <p class="bio">Peter Holloway is a business executive with extensive C-level and board leadership experience across multiple privately and publicly held companies. He is currently a Founder and Member of CVT Investments LLC. Previously, he served as founder, chairman and chief executive of a healthcare services company operating in the U.S. and internationally from 2003 to 2012, and later chaired several partner firms.</p>
  </article>
  <div class="foot-date">03 April 2024</div><div class="foot-page">Page No: 07</div>
</section>

<!-- How We Are Different -->
<section class="slide col-r row4">
  <div class="head"><svg width="469" height="37"><use href="#head-shape"/></svg><div class="brand">CVT</div><div class="head-title">How We Are Different</div></div>
  <div class="abs" style="left:23px;top:57px;width:425px">
    <h2 class="h-blue">Our Distinctive Approach</h2>
    <p class="body" style="line-height:12px;margin-top:1px">Unlike many funds that adhere to a rigid transaction structure, CVT collaborates directly with each company to customize investment structures and strategies that align with mutual objectives.</p>
  </div>
  <div class="feature" style="left:23px"><div class="fh bg-blue">Focused Portfolio</div><div class="fb bg-grey" style="height:57px">We prioritize a smaller portfolio to maximize returns for each Investment.</div></div>
  <div class="feature" style="left:129px"><div class="fh bg-grey">Problem-Solving<br>Strategy</div><div class="fb bg-blue" style="height:76px">Our approach is centered on addressing challenges and/or supporting milestones to unlock each company's full potential</div></div>
  <div class="feature" style="left:235px"><div class="fh bg-blue">Efficient Processes</div><div class="fb bg-grey" style="height:89px">CVT employs internal due diligence and document review procedures to ensure cost-effective and timely execution of opportunities.</div></div>
  <div class="feature" style="left:350px"><div class="fh bg-grey">Robust Network</div><div class="fb bg-blue" style="height:98px">We leverage our established network of professionals and investment partners to explore new opportunities.</div></div>
  <div class="foot-date">03 April 2024</div><div class="foot-page">Page No: 08</div>
</section>

</div>
</body>
</html>
```